Business Card Design

I already have a company logo for my company. I have a logo for the manufacturer we represent. I want a professional business card design.

```html
<!DOCTYPE html>
<html lang="en">
<head>
<meta charset="utf-8">
<title>Northgate Signal LLC – Business Card</title>
<link href="https://fonts.googleapis.com/css2?family=Open+Sans:wght@400;600;700;800&display=swap" rel="stylesheet">
<style>
  :root {
    --stage: #222223;
    --card-face: #1e1e22;
    --card-edge: #8a6a24;
    --gold: #b08a3a;
    --red: #e0222b;
    --white: #f2f2f2;
    --muted: #d8d8d8;
  }
  * { box-sizing: border-box; margin: 0; padding: 0; }
  html, body {
    width: 1200px; height: 780px; overflow: hidden;
    background: var(--stage);
    font-family: "Open Sans", Arial, sans-serif;
  }
  .stage {
    position: relative; width: 1200px; height: 780px;
    display: flex; align-items: center; justify-content: center; gap: 40px;
  }
  .card {
    position: relative; width: 540px; height: 310px;
    background: var(--card-face);
    border: 4px solid var(--card-edge);
    border-radius: 22px;
    overflow: hidden;
    box-shadow: 0 14px 30px rgba(0,0,0,.55);
  }
  .brand { display: flex; align-items: center; gap: 10px; }
  .brand-mark { width: 22px; height: 22px; background: var(--red); flex: none; }
  .brand-name {
    font-weight: 800; color: var(--white);
    letter-spacing: 1px; text-transform: uppercase; line-height: 1.15;
  }

  /* front */
  .card-front .brand { position: absolute; left: 40px; top: 50px; }
  .card-front .brand-name { font-size: 20px; }
  .divider { position: absolute; left: 0; top: 0; width: 100%; height: 100%; }
  .address {
    position: absolute; left: 40px; bottom: 32px;
    font-size: 12.5px; color: var(--muted); white-space: nowrap;
  }
  .contact-block { position: absolute; left: 322px; top: 100px; }
  .person-name { font-size: 25px; font-weight: 700; color: var(--red); line-height: 1.1; }
  .person-name .surname { color: var(--gold); }
  .person-title { font-size: 13px; color: var(--white); margin-top: 4px; }
  .contact-list { list-style: none; margin-top: 16px; }
  .contact-list li {
    display: flex; align-items: center; gap: 8px;
    font-size: 12.5px; color: var(--white); margin-bottom: 6px; white-space: nowrap;
  }
  .contact-list svg { width: 13px; height: 13px; flex: none; }

  /* back */
  .card-back { display: flex; align-items: center; justify-content: center; }
  .card-back .brand { gap: 14px; }
  .card-back .brand-mark { width: 34px; height: 34px; }
  .card-back .brand-name { font-size: 32px; }
</style>
</head>
<body>
<main class="stage">
  <section class="card card-front" aria-label="Card front">
    <div class="brand">
      <span class="brand-mark"></span>
      <span class="brand-name">Northgate<br>Signal LLC</span>
    </div>
    <svg class="divider" viewBox="0 0 532 302" aria-hidden="true">
      <line x1="300" y1="88" x2="232" y2="222" stroke="var(--gold)" stroke-width="1" opacity=".7"/>
    </svg>
    <p class="address">1840 Meadowlark Ave. Suite 310 Riverton, TX 75001</p>
    <div class="contact-block">
      <h1 class="person-name">Daniel <span class="surname">Kovar</span></h1>
      <p class="person-title">Managing Director</p>
      <ul class="contact-list">
        <li>
          <svg viewBox="0 0 16 16" aria-hidden="true"><path fill="var(--red)" d="M3.6 1.5l2.3 2.6-1.3 1.8c.9 1.9 2.4 3.4 4.3 4.3l1.8-1.3 2.6 2.3-1.2 2.3C7 13.3 2.7 9 2.2 2.7z"/></svg>
          (555) 214-7730
        </li>
        <li>
          <svg viewBox="0 0 16 16" aria-hidden="true"><rect x="1.5" y="3.5" width="13" height="9" rx="1" fill="var(--red)"/><path d="M2 4.2l6 4.6 6-4.6" stroke="var(--card-face)" stroke-width="1.3" fill="none"/></svg>
          hello@northgatesignal.com
        </li>
        <li>
          <svg viewBox="0 0 16 16" aria-hidden="true"><circle cx="8" cy="8" r="6.5" fill="var(--red)"/><path d="M1.5 8h13M8 1.5c-3 3.5-3 9.5 0 13M8 1.5c3 3.5 3 9.5 0 13" stroke="var(--card-face)" stroke-width="1" fill="none"/></svg>
          www.northgatesignal.com
        </li>
      </ul>
    </div>
  </section>

  <section class="card card-back" aria-label="Card back">
    <div class="brand">
      <span class="brand-mark"></span>
      <span class="brand-name">Northgate<br>Signal LLC</span>
    </div>
  </section>
</main>
</body>
</html>
```